Varnik Holdings — Business Card Design Brief
Overview
Design a double-sided business card for Varnik Holdings that highlights our two service arms: Varnik Communications (telecommunications) and Varnik Energy (business energy solutions). The card should feel smart and stand out when handed to clients.

Objectives
Showcase our areas of specialty clearly.
Reflect the overall Varnik / Varnik Holdings brand while acknowledging both arms.
Explore using both logos (Communications + Energy) or one unified logo, depending on the design.

Deliverables
One double-sided business card design (front + back).

Content & Copy
Front (preferred): Logo: Varnik / Varnik Holdings
Descriptor: Business Communications | Business Energy
Back:My contact details and company details
Core products: Business Mobile • Telephony • Internet • Business Energy Solutions

Brand & Visual Direction
We have a group logo currently tailored more toward telecoms, plus a separate Varnik Energy logo.
Please explore layouts that use both logos or just one, whichever works best.
Color: I wouldn't mind seeing an option using our the Blue/Purple gradient from our website (varnik-example.co.uk), but also open to non-gradient approaches and other colours..

Overall look: Smart, modern, and distinctive.
Format & Print Specs
Double-sided business card format. (Use a standard size

Must-Haves
Front: Varnik wording or Varnik Holdings wording with atleast 1 logo also on front “Business Communications | Business Energy.”

Back: Contact + company details and core products.
A design that stands out while remaining professional.

Nice-to-Have Options
A gradient version using our site’s Blue/Purple gradient.
A non-gradient version.
A dual-logo treatment versus a single-logo treatment.

Thanks
Owen

```html
<!DOCTYPE html>
<html lang="en">
<head>
<meta charset="utf-8">
<title>Varnik Holdings — Business Card</title>
<link href="https://fonts.googleapis.com/css2?family=Montserrat:wght@700;800&family=Roboto:wght@400&display=swap" rel="stylesheet">
<style>
  :root {
    --stage: #e6e6e6;
    --navy: #1b1763;
    --accent: #1a8ad8;
    --text: #444444;
    --rule: #cfcfcf;
    --sky: #0cb4e4;
    --royal: #0a5ad2;
    --white: #ffffff;
  }
  * { margin: 0; padding: 0; box-sizing: border-box; }
  html, body { width: 1200px; height: 1200px; overflow: hidden; background: var(--stage); }
  body { position: relative; font-family: "Roboto", Arial, sans-serif; }

  .card { position: absolute; width: 689px; height: 394px; overflow: hidden; }
  .card-front { left: 267px; top: 159px; background: var(--white); }
  .card-back { left: 262px; top: 653px; background: linear-gradient(180deg, var(--sky) 0%, var(--royal) 100%); }

  /* Front */
  .brand { position: absolute; right: 46px; top: 152px; display: flex; align-items: center; gap: 12px; }
  .brand-dot { width: 26px; height: 26px; border-radius: 50%; background: var(--accent); }
  .brand-name { font-family: "Montserrat", Arial, sans-serif; font-weight: 800; font-size: 46px; color: var(--navy); line-height: 1; letter-spacing: 0.5px; }

  .person { position: absolute; left: 48px; top: 224px; }
  .person-name { font-family: "Montserrat", Arial, sans-serif; font-weight: 700; font-size: 27px; color: var(--navy); line-height: 1.1; }
  .person-role { font-size: 16px; color: var(--accent); margin-top: 2px; }

  .contacts { position: absolute; left: 47px; top: 290px; list-style: none; }
  .contacts li { display: flex; align-items: center; gap: 10px; font-size: 16px; color: var(--text); height: 20.5px; }
  .contacts svg { width: 14px; height: 14px; fill: var(--navy); flex: none; }

  .address, .products { position: absolute; right: 46px; text-align: right; font-size: 16px; color: var(--text); line-height: 21px; }
  .address { top: 224px; }
  .products { top: 288px; }
  .divider { position: absolute; left: 157px; right: 46px; top: 281px; height: 1px; background: var(--rule); }

  .footer-band { position: absolute; left: 0; bottom: 0; width: 689px; height: 33px; }
  .footer-url { position: absolute; right: 42px; bottom: 9px; font-size: 16px; color: var(--white); }

  /* Back */
  .arm { position: absolute; top: 0; width: 300px; height: 394px; text-align: center; color: var(--white); }
  .arm-comms { left: 56px; }
  .arm-energy { left: 333px; }
  .arm-name { position: absolute; left: 0; right: 0; top: 160px; font-family: "Montserrat", Arial, sans-serif; font-weight: 800; font-size: 24px; line-height: 1.15; }
  .arm-label { position: absolute; left: 0; right: 0; top: 268px; font-size: 16px; letter-spacing: 0.2px; }
  .back-divider { position: absolute; left: 346px; top: 114px; width: 1px; height: 167px; background: rgba(255,255,255,0.75); }
</style>
</head>
<body>

<section class="card card-front" aria-label="Card front">
  <div class="brand">
    <span class="brand-dot"></span>
    <span class="brand-name">VARNIK</span>
  </div>

  <div class="person">
    <p class="person-name">MARCUS HALE</p>
    <p class="person-role">President</p>
  </div>

  <ul class="contacts">
    <li>
      <svg viewBox="0 0 24 24" aria-hidden="true"><path d="M6.6 10.8a15.1 15.1 0 0 0 6.6 6.6l2.2-2.2c.3-.3.7-.4 1-.2 1.1.4 2.3.6 3.6.6.6 0 1 .4 1 1V20c0 .6-.4 1-1 1A17 17 0 0 1 3 4c0-.6.4-1 1-1h3.5c.6 0 1 .4 1 1 0 1.3.2 2.5.6 3.6.1.3 0 .7-.2 1z"/></svg>
      020-555-0148
    </li>
    <li>
      <svg viewBox="0 0 24 24" aria-hidden="true"><path d="M7 1h10a2 2 0 0 1 2 2v18a2 2 0 0 1-2 2H7a2 2 0 0 1-2-2V3a2 2 0 0 1 2-2zm0 3v15h10V4zm5 16.2a1 1 0 1 0 0 2 1 1 0 0 0 0-2z"/></svg>
      020-555-0192
    </li>
    <li>
      <svg viewBox="0 0 24 24" aria-hidden="true"><path d="M2 5h20v14H2zm2 2v.5l8 5 8-5V7zm0 3v7h16v-7l-8 5z"/></svg>
      info@varnik-example.co.uk
    </li>
  </ul>

  <p class="address">42 Harbour Row<br>Bristol, United Kingdom BS1 5XX</p>
  <div class="divider"></div>
  <p class="products">Business Mobile<br>Telephony • Internet<br>Business Energy Solutions</p>

  <svg class="footer-band" viewBox="0 0 689 33" preserveAspectRatio="none" aria-hidden="true">
    <defs>
      <linearGradient id="stripe" x1="0" x2="1" y1="0" y2="0">
        <stop offset="0" stop-color="#1a5fd6"/>
        <stop offset="0.6" stop-color="#14b4e8"/>
        <stop offset="1" stop-color="#1a6ad8"/>
      </linearGradient>
    </defs>
    <rect x="0" y="0" width="689" height="33" fill="#1b1763"/>
    <path d="M0 0 H436 L428 15 H0 Z" fill="url(#stripe)"/>
    <path d="M436 0 H446 Q438 6 436 15 L428 15 Z" fill="#ffffff"/>
    <rect x="0" y="15" width="430" height="2" fill="#ffffff"/>
  </svg>
  <p class="footer-url">www.varnik-example.co.uk</p>
</section>

<section class="card card-back" aria-label="Card back">
  <div class="arm arm-comms">
    <p class="arm-name">Varnik<br>Communications</p>
    <p class="arm-label">BUSINESS COMMUNICATIONS</p>
  </div>
  <div class="back-divider"></div>
  <div class="arm arm-energy">
    <p class="arm-name">Varnik<br>Energy</p>
    <p class="arm-label">BUSINESS ENERGY</p>
  </div>
</section>

</body>
</html>
```